Website Design for Videographer

I am looking to update my website - www.brinolvaske.com. I am a wedding videographer who specialises in natural and documentary videography.

The website will be built by my designer using the Wordpress Plinthworx framework.

Requirements;
I want the website to have a clean white look mixed in with video footage.
Needs to be classy. At the moment my website uses a lot of Gold. On the new look I DO NOT want gold.

Need a web and mobile design for the following 12 pages;

* Home page (need to have example videos and text)
* About (this is about me and my service)
* Videos (examples of my work)
* Testimonials
* Packages
* Contact
* Content (this is to show social media content that I am making in a vertical format and advertise this service).
* Blog (index page for blog)
* Blog pages (individual pages for blog content)
* Wedding Venues Index Page (https://brinolvaske.com/north-east-wedding-venues/)
* Individual venue pages (https://brinolvaske.com/north-east-wedding-venues/marlow-tendle-lodge-wedding-videos/) - Needs to show videos, photos, text as is on the current page.
* Venue Tours (https://brinolvaske.com/wedding-venue-tours/)

My current logo is attached however on the website I want to go for a black and white style for it.

Example styles I like however must not be copied.
https://joswelbrant.co.uk/about/
https://oakandripple.co.uk/ (if done in white)
https://tumblemothpictures.co.uk/

Target Market(s)

Couples getting married aged 25-35

Industry/Entity Type

Weddings

Number of Pages Required

5+ page

Font styles to use
Sans Serif

Requirements
Must have
• A classy look, black and white, use videos and photos.
Should not have
• Gold colour

```html
<!DOCTYPE html>
<html lang="en">
<head>
<meta charset="utf-8">
<title>Brin Olvaske Wedding Films – Packages</title>
<link rel="stylesheet" href="https://fonts.googleapis.com/css2?family=Cinzel:wght@400;500&family=Poppins:wght@400;500;600&family=Anton&display=swap">
<style>
:root{
  --ink:#0a0a0a;
  --white:#ffffff;
  --mist:#f2f2f2;
  --slate:#858585;
  --footer:#676565;
  --rule:#bdbdbd;
  --text:#3a3a3a;
  --alert:#f20c0c;
  --leaf-dark:#2f4424;
  --leaf:#5b7a3e;
  --sky:#cfd6d0;
}
*{margin:0;padding:0;box-sizing:border-box}
html,body{width:1200px;height:3774px;overflow:hidden;background:var(--white)}
body{position:relative;font-family:"Poppins",sans-serif;color:var(--ink)}
.abs{position:absolute}

/* header */
.site-header{position:absolute;left:0;top:0;width:1200px;height:125px;background:var(--white)}
.nav-link{position:absolute;top:54px;font-size:12.5px;letter-spacing:.2px;color:var(--ink);text-decoration:none;text-transform:uppercase}
.brand{position:absolute;left:600px;transform:translateX(-50%);text-align:center;color:var(--ink);font-family:"Poppins",sans-serif;font-weight:500;text-transform:uppercase;white-space:nowrap}
.brand-name{font-size:19px;letter-spacing:5px;line-height:1}
.brand-sub{font-size:9px;letter-spacing:5px;margin-top:8px;line-height:1}
.site-header .brand{top:68px}
.btn-enquire{position:absolute;left:998px;top:35px;width:134px;height:46px;background:var(--ink);color:var(--white);font-size:13.5px;font-weight:500;display:flex;align-items:center;justify-content:center;text-decoration:none}

/* hero */
.hero-band{position:absolute;left:0;top:125px;width:1200px;height:344px;background:var(--mist)}
.hero-title{position:absolute;left:0;top:225px;width:1200px;text-align:center;font-family:"Cinzel",serif;font-weight:400;font-size:58px;line-height:63px;letter-spacing:2px;color:var(--ink)}
.btn-book{position:absolute;left:508px;top:372px;width:222px;height:62px;background:var(--ink);color:var(--white);font-size:17px;font-weight:500;display:flex;align-items:center;justify-content:center;text-decoration:none}
.hero-photo{position:absolute;left:0;top:469px;width:1200px;height:643px;
  background:linear-gradient(180deg,var(--sky) 0%,#8a9a7c 12%,var(--leaf) 35%,#6d7f62 55%,var(--leaf-dark) 80%,#3d5a28 100%)}

/* packages */
.section-title{position:absolute;left:0;width:1200px;text-align:center;font-family:"Cinzel",serif;font-weight:400;font-size:57px;letter-spacing:2px;line-height:1;color:var(--ink)}
.intro{position:absolute;left:90px;top:1298px;width:1020px;text-align:center;font-size:14.2px;line-height:28px;color:#222}

.card{position:absolute;top:1477px;width:331px;background:var(--white);box-shadow:0 0 7px rgba(0,0,0,.18);display:flex;flex-direction:column}
.card-head{height:123px;background:var(--slate);color:var(--white);display:flex;flex-direction:column;align-items:center;justify-content:center;text-align:center}
.card-name{font-size:35px;font-weight:600;line-height:1.1;letter-spacing:.5px}
.card-note{font-size:11.5px;line-height:13.5px;margin-top:4px;padding:0 20px}
.card-body{padding:36px 30px 0 28px;flex:1;display:flex;flex-direction:column}
.feature{margin-bottom:38px}
.feature-title{display:flex;align-items:center;gap:14px;font-size:16.5px;font-weight:500;text-transform:uppercase;color:var(--ink);margin-bottom:10px}
.tick{width:27px;height:27px;flex:none}
.feature-text{font-size:13.6px;line-height:24px;color:var(--text);text-align:justify;letter-spacing:.3px}
.coverage{margin:auto -10px 14px -8px;height:106px;background:var(--slate);color:var(--white);font-size:14px;line-height:24px;padding:18px 20px;letter-spacing:.2px}

.status{position:absolute;left:0;top:2818px;width:1200px;text-align:center;font-family:"Anton",sans-serif;font-size:66px;line-height:1;color:var(--alert)}

/* footer */
.site-footer{position:absolute;left:0;top:3418px;width:1200px;height:356px;background:var(--footer);color:var(--white)}
.site-footer .brand{color:var(--white);top:112px}
.footer-rule{position:absolute;height:1px;background:var(--rule)}
.footer-link{position:absolute;top:221px;font-size:12.5px;color:var(--white);text-decoration:none;text-transform:uppercase;transform:translateX(-50%)}
.footer-enquire{position:absolute;left:527px;top:205px;width:137px;height:51px;border:1.5px solid var(--white);color:var(--white);font-size:15px;display:flex;align-items:center;justify-content:center;text-decoration:none}
.copyright{position:absolute;left:66px;top:312px;font-size:10px;color:var(--white)}
.social{position:absolute;top:299px;width:38px;height:38px;border-radius:50%;background:var(--white)}
</style>
</head>
<body>

<header class="site-header">
  <a class="nav-link" style="left:69px">Home</a>
  <a class="nav-link" style="left:142px">About Brin</a>
  <a class="nav-link" style="left:264px">Wedding Films</a>
  <a class="nav-link" style="left:397px">Blog</a>
  <div class="brand">
    <div class="brand-name">Brin Olvaske</div>
    <div class="brand-sub">Wedding Films</div>
  </div>
  <a class="nav-link" style="left:771px">Testimonials</a>
  <a class="nav-link" style="left:889px">Packages</a>
  <a class="btn-enquire">ENQUIRE</a>
</header>

<section>
  <div class="hero-band"></div>
  <h1 class="hero-title">NORTH EAST WEDDING<br>VIDEOGRAPHER</h1>
  <a class="btn-book">BOOK WITH ME</a>
  <div class="hero-photo" role="img" aria-label="Photo of a bride and groom embracing beside a lake surrounded by ferns and forest"></div>
</section>

<section>
  <h2 class="section-title" style="top:1216px">WEDDING VIDEOGRAPHY PACKAGES</h2>
  <p class="intro">Are you the kind of couple who wants to soak up every moment rather than spending your big day striking poses? Do you appreciate the little, unplanned surprises that come with real life? If that’s you, then we’re on the same page! I’m all about capturing the natural, unscripted moments that make your wedding truly yours. Your wedding isn’t a Hollywood production; it’s a real event with spontaneous laughter, tears, and joy. Trust me to document all of it, just as it unfolds. How does that sound for making your wedding memories truly authentic?</p>

  <article class="card" style="left:70px;height:866px">
    <div class="card-head"><div class="card-name">SIGNATURE</div></div>
    <div class="card-body">
      <div class="feature">
        <div class="feature-title"><svg class="tick" viewBox="0 0 24 24"><circle cx="12" cy="12" r="12" fill="#0a0a0a"/><path d="M6.5 12.5l3.7 3.6 7.4-7.6" fill="none" stroke="#fff" stroke-width="2.4" stroke-linecap="round" stroke-linejoin="round"/></svg>Highlights Video</div>
        <p class="feature-text">A 6-7 minute highlight video capturing key and candid moments from your special day. Featuring audio from your ceremony and speeches, paired with high-quality, unlicensed music.</p>
      </div>
      <div class="feature">
        <div class="feature-title"><svg class="tick" viewBox="0 0 24 24"><circle cx="12" cy="12" r="12" fill="#0a0a0a"/><path d="M6.5 12.5l3.7 3.6 7.4-7.6" fill="none" stroke="#fff" stroke-width="2.4" stroke-linecap="round" stroke-linejoin="round"/></svg>Ceremony Recording</div>
        <p class="feature-text">The complete recording of your wedding, filmed with a minimum of three cameras. Professionally captured audio ensures every word is clearly heard.</p>
      </div>
      <div class="feature">
        <div class="feature-title"><svg class="tick" viewBox="0 0 24 24"><circle cx="12" cy="12" r="12" fill="#0a0a0a"/><path d="M6.5 12.5l3.7 3.6 7.4-7.6" fill="none" stroke="#fff" stroke-width="2.4" stroke-linecap="round" stroke-linejoin="round"/></svg>Speeches Recording</div>
        <p class="feature-text">Your wedding speeches and toasts, recorded in full with at least three cameras. Professional microphones guarantee every word is captured clearly.</p>
      </div>
      <div class="coverage">Coverage from 2 hours before ceremony to 15 minutes after first dance.</div>
    </div>
  </article>

  <article class="card" style="left:437px;height:759px">
    <div class="card-head"><div class="card-name">GOLD</div><div class="card-note">Everything in the signature package<br>(highlights, ceremony and speeches) plus</div></div>
    <div class="card-body">
      <div class="feature">
        <div class="feature-title"><svg class="tick" viewBox="0 0 24 24"><circle cx="12" cy="12" r="12" fill="#0a0a0a"/><path d="M6.5 12.5l3.7 3.6 7.4-7.6" fill="none" stroke="#fff" stroke-width="2.4" stroke-linecap="round" stroke-linejoin="round"/></svg>Extended Film</div>
        <p class="feature-text">A feature-length video, running at least 60 minutes, showcasing extensive footage and moments from morning preparations to your evening celebration. This is a future heirloom for your family, capturing often unseen moments of your wedding day to be cherished for years to come.</p>
      </div>
      <div class="feature">
        <div class="feature-title"><svg class="tick" viewBox="0 0 24 24"><circle cx="12" cy="12" r="12" fill="#0a0a0a"/><path d="M6.5 12.5l3.7 3.6 7.4-7.6" fill="none" stroke="#fff" stroke-width="2.4" stroke-linecap="round" stroke-linejoin="round"/></svg>Teaser Film</div>
        <p class="feature-text">A short teaser video capturing the key highlights of your wedding day to build excitement. Delivered within 72 hours post-wedding. Perfect for sharing on social media.</p>
      </div>
      <div class="coverage">Coverage from 2 hours before ceremony to 15 minutes after first dance.</div>
    </div>
  </article>

  <article class="card" style="left:803px;height:759px">
    <div class="card-head"><div class="card-name">PLATINUM</div><div class="card-note">Everything in the gold package<br>(highlights, ceremony, speeches, long video and teaser) plus</div></div>
    <div class="card-body">
      <div class="feature">
        <div class="feature-title"><svg class="tick" viewBox="0 0 24 24"><circle cx="12" cy="12" r="12" fill="#0a0a0a"/><path d="M6.5 12.5l3.7 3.6 7.4-7.6" fill="none" stroke="#fff" stroke-width="2.4" stroke-linecap="round" stroke-linejoin="round"/></svg>Longer Feature Film</div>
        <p class="feature-text">Any even longer feature film featuring more moments from your wedding day.</p>
      </div>
      <div class="feature">
        <div class="feature-title"><svg class="tick" viewBox="0 0 24 24"><circle cx="12" cy="12" r="12" fill="#0a0a0a"/><path d="M6.5 12.5l3.7 3.6 7.4-7.6" fill="none" stroke="#fff" stroke-width="2.4" stroke-linecap="round" stroke-linejoin="round"/></svg>USB</div>
        <p class="feature-text">You will receive your videos on a crystal USB drive, presented in a branded gift box.</p>
      </div>
      <div class="feature">
        <div class="feature-title"><svg class="tick" viewBox="0 0 24 24"><circle cx="12" cy="12" r="12" fill="#0a0a0a"/><path d="M6.5 12.5l3.7 3.6 7.4-7.6" fill="none" stroke="#fff" stroke-width="2.4" stroke-linecap="round" stroke-linejoin="round"/></svg>Video Images</div>
        <p class="feature-text">You will receive at least 100 screen images, perfect for sharing on social media.</p>
      </div>
      <div class="coverage">Coverage from 3 hours before ceremony until 11 pm</div>
    </div>
  </article>
</section>

<section>
  <h2 class="section-title" style="top:2473px">EVERY PACKAGE INCLUDES</h2>
  <p class="status">DESIGN UNDER PROCESS...</p>
</section>

<footer class="site-footer">
  <div class="footer-rule" style="left:69px;top:135px;width:379px"></div>
  <div class="brand">
    <div class="brand-name">Brin Olvaske</div>
    <div class="brand-sub">Wedding Films</div>
  </div>
  <div class="footer-rule" style="left:756px;top:135px;width:379px"></div>

  <a class="footer-link" style="left:208px">Home</a>
  <a class="footer-link" style="left:304px">About Brin</a>
  <a class="footer-link" style="left:434px">Wedding Films</a>
  <a class="footer-enquire">ENQUIRE</a>
  <a class="footer-link" style="left:733px">Blog</a>
  <a class="footer-link" style="left:826px">Testimonials</a>
  <a class="footer-link" style="left:935px">Packages</a>

  <div class="footer-rule" style="left:69px;top:290px;width:1066px"></div>
  <p class="copyright">Copyright 2010 - 2024 © Brin Olvaske Wedding Films Limited. All Rights Reserved</p>
  <span class="social" style="left:983px" aria-label="Social link"></span>
  <span class="social" style="left:1040px" aria-label="Social link"></span>
  <span class="social" style="left:1097px" aria-label="Social link"></span>
</footer>

</body>
</html>
```